Redo our website for our Robotics company

We sell robotic equipment to the restaurant industry. Our current robot, is a cooking robot that cooks up to 15 lbs of food. We will provide a prior website as well as brand guidelines. We plan on using wordpress and take advantage of wordpress's visual (no code) editor.

Current website - https://kelvatrix88.com/ (please note we are only selling Tammo now and no longer selling Plavo+

We want someone to take our existing content and design the website as well as layout our content we provide. Here's a suggested site layout:

✅ KelvaTrix88 Website Wireframe / Site Map
1. Home

Purpose: Introduce Tammo, establish credibility, drive demo requests.

Sections:

Hero Section

Headline: “Meet Tammo — Your New Robotic Chef for High-Volume, Consistent Cooking.”

Sub-headline: Increase throughput. Reduce labor. Deliver perfect food every time.

CTA: Request a Demo + Watch Tammo Cook

Visual: Video loop or hero animation of Tammo in action.

How Tammo Works (3-4 steps)

Step cards: Load Ingredients → Select Recipe → Tammo Cooks → Serve

Icons and short explanations.

Key Benefits

Labor savings

Zero inconsistency

24/7 uptime

Throughput increases (30–50% faster)

Health & safety compliance

Who It’s For

QSR restaurants

Fast casual

Catering/commissaries

Ghost kitchens

Case Studies / Testimonials

Logo bar + quotes

“Tammo helped us reduce cooking times by 40%.”

Video Section

“Watch Tammo cook a full batch from start to finish.”

CTA Section

Big banner: Book a Demo

2. Product: “Meet Tammo”

Purpose: Deep dive into hardware, software, safety, reliability.

Sections:

Overview

What Tammo is

What tasks it automates

Where it fits in a kitchen

Hardware Features

High-temperature cooking chamber

Precision sensors

Automated stirring

Automated dispensing

Safety mechanisms (locking lids, auto-shutoff)

Software & AI

Recipe automation

IoT dashboard

Remote monitoring

Predictive maintenance

Specs Table

Dimensions

Power requirements

Capacity (lbs per batch)

Safety certifications

Gallery

Close-ups, installation photos, process shots

CTA: Request a Demo

3. Solutions

Purpose: Show that Tammo solves real operational problems.

Sub-pages or sections:

For Quick-Service Restaurants

Reduce labor cost

Speed up peak-hour demand

For Catering & Commissaries

Large-batch consistency

Automate repetitive cooking tasks

For High-Growth Chains

Replicable quality across multiple locations

Centralized recipe control

Each solution page includes:

A problem statement

How Tammo solves it

Metrics / KPIs

Relevant testimonial

CTA

4. ROI / Economics

Purpose: Sell the financial story clearly.

Sections:

Savings Calculator

Labor hours saved

Cost savings

Throughput increases

Food waste reduction

Before & After Comparison

Traditional kitchen vs. robotic kitchen

Sample ROI

“Payback in as little as 3–6 months.”

Download Full ROI Report (PDF)

5. Case Studies

Purpose: Social proof + real results.

Structure for each case study:

Customer background

Problem

Implementation

KPIs achieved

Labor savings

Consistency improvements

Cooking speed

Quote + photos/video

6. Pricing

Purpose: Start a commercial conversation.

Include:

Subscription model (monthly / annual)

Hardware leasing or purchase options

Installation + training

Support level

CTA to book a sales call

7. About

Purpose: Build trust.

Sections:

Mission statement

Founding team

Advisors/partners

“Why we built Tammo”

8. Resources

Purpose: SEO + education.

Subpages:

Blog (e.g., “The Future of Automated Kitchens”)

Whitepapers

Technical documentation

Product videos

9. Contact

General inquiry form

Sales contact

Support portal

Careers

```html
<!DOCTYPE html>
<html lang="en">
<head>
<meta charset="utf-8">
<title>KelvaTrix88 — Meet Tammo</title>
<link href="https://fonts.googleapis.com/css2?family=Montserrat:wght@600;700;800&family=Lato:ital,wght@0,400;0,700;1,400&display=swap" rel="stylesheet">
<style>
:root{
  --navy:#0d2d5e;
  --navy-deep:#0c2a57;
  --orange:#f48b4f;
  --ink:#1d2433;
  --muted:#4a4f5a;
  --band:#e6eef8;
  --line:#d9dde3;
  --white:#ffffff;
  --steel-1:#4a5b6e;
  --steel-2:#2a3646;
}
*{box-sizing:border-box;margin:0;padding:0}
html,body{width:1200px;height:3640px;overflow:hidden;background:var(--white)}
body{position:relative;font-family:'Lato',sans-serif;color:var(--ink)}
.abs{position:absolute}
h1,h2,.head{font-family:'Montserrat',sans-serif}
.accent{color:var(--orange)}

/* nav */
.site-nav{left:0;top:0;width:1200px;height:72px;background:var(--white);border-bottom:1px solid var(--line)}
.brand{left:110px;top:18px;display:flex;align-items:center;gap:8px;font-family:'Montserrat',sans-serif;font-weight:800;font-size:28px;color:var(--navy)}
.brand .mark{width:22px;height:22px;background:var(--orange);border-radius:4px}
.nav-links{right:110px;top:26px;display:flex;gap:30px;font-size:15px;color:var(--ink)}

/* hero */
.hero{left:0;top:72px;width:1200px;height:555px;background:linear-gradient(180deg,#5b6f86 0%,#3c4c60 55%,#2f3b4a 100%)}
.hero-panel{left:93px;top:70px;width:760px;height:350px;background:rgba(24,45,85,.55)}
.hero h1{left:110px;top:90px;width:840px;font-size:51px;line-height:64px;font-weight:800;color:var(--white)}
.hero-sub{left:113px;top:300px;font-size:18px;font-weight:700;color:var(--white)}
.btn{display:inline-flex;align-items:center;justify-content:center;background:var(--orange);color:var(--white);font-size:17px;height:46px;clip-path:polygon(6% 0,100% 0,94% 100%,0 100%)}
.hero .btn-demo{left:113px;top:346px;width:178px}
.hero .btn-watch{left:295px;top:346px;width:193px}

/* section titles */
.section-title{width:1200px;left:0;text-align:center;font-size:38px;font-weight:700;color:var(--navy)}

/* steps */
.step{top:780px;width:230px;height:230px;border:1px solid var(--line);border-radius:4px;box-shadow:0 2px 6px rgba(0,0,0,.12);text-align:center;background:var(--white)}
.step svg{margin-top:16px}
.step h3{font-family:'Montserrat',sans-serif;font-weight:600;font-size:19px;margin:6px 0 10px}
.step p{font-size:14.5px;line-height:25.5px;color:var(--muted);padding:0 24px}

/* audience */
.audience{left:0;top:1095px;width:1200px;height:622px;background:var(--band)}
.media{background:linear-gradient(160deg,#8b97a3 0%,#5c6672 45%,#c7ccd1 100%);border-radius:4px}
.audience .media{left:108px;top:97px;width:446px;height:439px;box-shadow:0 3px 10px rgba(0,0,0,.18)}
.audience h2{left:643px;top:72px;font-size:38px;font-weight:700;color:var(--navy)}
.aud-list{left:643px;top:145px;width:440px}
.aud-item{margin-bottom:20px}
.aud-item h4{display:flex;align-items:center;gap:16px;font-size:18px;font-weight:400;color:var(--ink);margin-bottom:14px}
.aud-item p{font-size:14px;line-height:26px;color:var(--muted)}

/* benefits */
.benefit{width:312px;height:153px}
.benefit .corner{left:0;top:0;width:135px;height:153px;background:var(--navy);border-radius:4px}
.benefit .card{left:8px;top:6px;width:304px;height:140px;background:var(--white);box-shadow:0 2px 6px rgba(0,0,0,.14)}
.benefit svg{position:absolute;left:12px;top:40px}
.benefit .divider{left:100px;top:22px;width:1px;height:96px;background:var(--line)}
.benefit h4{left:112px;top:18px;font-size:15px;font-weight:700;color:var(--ink)}
.benefit p{left:113px;top:46px;width:190px;font-size:13px;line-height:25.5px;color:var(--muted)}
.benefit a{left:113px;top:104px;font-size:14px;font-style:italic;color:var(--ink);text-decoration:underline}
.btn-book{left:512px;top:2246px;width:177px}

/* video */
.video{left:112px;top:2374px;width:976px;height:469px;border-radius:6px}
.play{left:560px;top:2570px}

/* testimonials */
.quote-card{top:2995px;width:305px;height:193px;background:var(--white);border:1px solid var(--line);box-shadow:0 2px 7px rgba(0,0,0,.13)}
.avatar{left:18px;top:32px;width:80px;height:80px;border-radius:50%;background:linear-gradient(180deg,#cfd6de,#8f9aa6)}
.quote-card .name{left:118px;top:52px;font-size:17px;font-weight:700;color:var(--ink)}
.quote-card .role{left:118px;top:77px;font-size:12.5px;color:var(--navy)}
.quote-card .stars{left:117px;top:92px}
.quote-card .qmark{right:20px;top:16px;font-family:'Montserrat',sans-serif;font-weight:800;font-size:34px;color:var(--orange)}
.quote-card p{left:20px;top:140px;width:265px;font-size:13px;line-height:20px;color:var(--muted);text-align:justify}
.arrow{top:3076px;width:24px;height:24px;border-radius:50%}

/* footer */
.site-footer{left:0;top:3272px;width:1200px;height:368px;background:var(--navy-deep);color:var(--white)}
.site-footer .brand{left:110px;top:92px;color:var(--white)}
.socials{left:110px;top:168px;display:flex;gap:10px}
.socials span{width:21px;height:21px;border-radius:50%;background:var(--white)}
.f-col h5{font-family:'Montserrat',sans-serif;font-weight:600;font-size:20px;margin-bottom:18px}
.f-col ul{list-style:none}
.f-col li{font-size:15px;margin-bottom:14px;display:flex;align-items:flex-start;gap:14px;line-height:22px}
.f-col li .dot{width:7px;height:7px;border-radius:50%;background:var(--white);margin-top:8px}
.f-rule{left:110px;top:318px;width:980px;height:1px;background:rgba(255,255,255,.3)}
.copyright{left:0;top:338px;width:1200px;text-align:center;font-size:15px}
</style>
</head>
<body>

<header class="abs site-nav">
  <div class="abs brand"><span class="mark"></span>KelvaTrix88</div>
  <nav class="abs nav-links"><span>Home</span><span>Meet Tammo</span><span>Solutions</span><span>Case Studies</span><span>About Us</span><span>Contact Us</span></nav>
</header>

<section class="abs hero" role="img" aria-label="Row of Tammo cooking robots in a commercial kitchen">
  <div class="abs hero-panel"></div>
  <h1 class="abs">Meet Tammo — Your New Robotic Chef for High-Volume, Consistent Cooking</h1>
  <p class="abs hero-sub">Increase throughput. Reduce labor. Deliver perfect food every time.</p>
  <a class="abs btn btn-demo">Request a Demo</a>
  <a class="abs btn btn-watch">Watch Tammo Cook</a>
</section>

<h2 class="abs section-title" style="top:697px">How Tammo <span class="accent">Works</span></h2>

<div class="abs step" style="left:110px">
  <svg width="64" height="64" viewBox="0 0 64 64" fill="none" stroke="#1d2433" stroke-width="2"><path d="M8 34h48c0 12-10 18-24 18S8 46 8 34z"/><path d="M8 34h48" stroke="#f48b4f"/><circle cx="22" cy="22" r="5" stroke="#f48b4f"/><circle cx="38" cy="16" r="4"/><circle cx="46" cy="26" r="4" stroke="#f48b4f"/><path d="M30 8l2 6"/></svg>
  <h3>Load Ingredients</h3>
  <p>Add up to 15 lbs of ingredients per batch into Tammo's high-capacity cooking chamber.</p>
</div>
<div class="abs step" style="left:360px">
  <svg width="64" height="64" viewBox="0 0 64 64" fill="none" stroke="#1d2433" stroke-width="2"><rect x="8" y="8" width="16" height="16"/><rect x="30" y="8" width="16" height="16"/><rect x="8" y="30" width="16" height="16"/><path d="M34 16l4 4 8-10" stroke="#f48b4f"/><path d="M36 56V34a3 3 0 016 0v10l10 2v10" stroke="#f48b4f"/></svg>
  <h3>Select Recipe</h3>
  <p>Choose from a library of preloaded recipes or run your custom programmed recipes.</p>
</div>
<div class="abs step" style="left:610px">
  <svg width="64" height="64" viewBox="0 0 64 64" fill="none" stroke="#1d2433" stroke-width="2"><path d="M10 22h44v10c0 12-10 22-22 22S10 44 10 32z"/><path d="M24 22c0-6 4-10 8-10s8 4 8 10"/><circle cx="32" cy="38" r="9" stroke="#f48b4f"/><path d="M32 33v5l3 3" stroke="#f48b4f"/><path d="M4 26h6M54 26h6"/></svg>
  <h3>Tammo Cooks</h3>
  <p>Tammo automatically handles temperature control, stirring, timing and safety monitoring.</p>
</div>
<div class="abs step" style="left:860px">
  <svg width="64" height="64" viewBox="0 0 64 64" fill="none" stroke="#1d2433" stroke-width="2"><path d="M10 34a22 22 0 0144 0z"/><circle cx="32" cy="10" r="2"/><path d="M6 34h52"/><path d="M14 44h20l12-6 6 4-16 10H14" stroke="#f48b4f"/></svg>
  <h3>Serve</h3>
  <p>Each batch comes out perfectly cooked and consistent, ready for plating or packaging.</p>
</div>

<section class="abs audience">
  <div class="abs media" role="img" aria-label="Tammo robots cooking a stir-fry batch"></div>
  <h2 class="abs">Who <span class="accent">It's For</span></h2>
  <div class="abs aud-list">
    <div class="aud-item"><h4><svg width="26" height="20" viewBox="0 0 26 20"><path d="M2 2l8 8-8 8M13 2l8 8-8 8" fill="none" stroke="#f48b4f" stroke-width="3.5"/></svg>Quick-Service Restaurants (QSR)</h4><p>Run peak-hour operations smoothly with consistent production and minimal staff pressure.</p></div>
    <div class="aud-item"><h4><svg width="26" height="20" viewBox="0 0 26 20"><path d="M2 2l8 8-8 8M13 2l8 8-8 8" fill="none" stroke="#f48b4f" stroke-width="3.5"/></svg>Fast Casual Restaurants</h4><p>Maintain flavor consistency and reduce operational bottlenecks as you scale.</p></div>
    <div class="aud-item"><h4><svg width="26" height="20" viewBox="0 0 26 20"><path d="M2 2l8 8-8 8M13 2l8 8-8 8" fill="none" stroke="#f48b4f" stroke-width="3.5"/></svg>Catering &amp; Commissaries</h4><p>Cook large batches faster while cutting labor hours dramatically.</p></div>
    <div class="aud-item"><h4><svg width="26" height="20" viewBox="0 0 26 20"><path d="M2 2l8 8-8 8M13 2l8 8-8 8" fill="none" stroke="#f48b4f" stroke-width="3.5"/></svg>Ghost Kitchens</h4><p>Increase output across multiple brands with one autonomous cooking system.</p></div>
  </div>
</section>

<h2 class="abs section-title" style="top:1786px">Key <span class="accent">Benefits</span></h2>

<div class="abs benefit" style="left:110px;top:1875px"><div class="abs corner"></div><div class="abs card">
  <svg width="74" height="60" viewBox="0 0 74 60" fill="none" stroke="#1d2433" stroke-width="2"><circle cx="26" cy="26" r="9"/><path d="M10 58c0-10 7-18 16-18s16 8 16 18"/><path d="M14 20h24" stroke="#f48b4f"/><circle cx="54" cy="14" r="10" stroke="#f48b4f"/><path d="M54 9v10"/><path d="M54 26v20M46 46h16"/></svg>
  <div class="abs divider"></div><h4 class="abs">Reduce Labor Costs</h4><p class="abs">Automate repetitive cooking tasks and reallocate staff to</p><a class="abs">Read More</a></div></div>
<div class="abs benefit" style="left:443px;top:1875px"><div class="abs corner"></div><div class="abs card">
  <svg width="74" height="60" viewBox="0 0 74 60" fill="none" stroke="#1d2433" stroke-width="2"><circle cx="24" cy="24" r="7"/><circle cx="48" cy="24" r="7"/><path d="M12 50c0-8 5-14 12-14s12 6 12 14M36 50c0-8 5-14 12-14s12 6 12 14"/><circle cx="36" cy="50" r="5" stroke="#f48b4f"/><path d="M20 8l3 6M36 6v7M52 8l-3 6" stroke="#f48b4f"/></svg>
  <div class="abs divider"></div><h4 class="abs">Zero Inconsistency</h4><p class="abs">Automate repetitive cooking tasks and reallocate staff to</p><a class="abs">Read More</a></div></div>
<div class="abs benefit" style="left:776px;top:1875px"><div class="abs corner"></div><div class="abs card">
  <svg width="74" height="60" viewBox="0 0 74 60" fill="none" stroke="#1d2433" stroke-width="2"><path d="M8 44a28 28 0 0156 0z"/><path d="M36 44l12-14" stroke="#f48b4f"/><circle cx="52" cy="16" r="8" stroke="#f48b4f"/><path d="M14 44h-6M64 44h-6"/></svg>
  <div class="abs divider"></div><h4 class="abs">30–50% Faster Throughput</h4><p class="abs">Tammo completes large-batch cooking significantly faster</p><a class="abs">Read More</a></div></div>
<div class="abs benefit" style="left:110px;top:2053px"><div class="abs corner"></div><div class="abs card">
  <svg width="74" height="60" viewBox="0 0 74 60" fill="none" stroke="#1d2433" stroke-width="2"><path d="M62 30a26 26 0 11-8-18" /><path d="M56 4v10H46" stroke="#f48b4f"/><text x="12" y="37" font-family="Montserrat,sans-serif" font-weight="700" font-size="17" fill="#1d2433" stroke="none">24/7</text></svg>
  <div class="abs divider"></div><h4 class="abs">24/7 Reliable Uptime</h4><p class="abs">Automate repetitive cooking tasks and reallocate staff to</p><a class="abs">Read More</a></div></div>
<div class="abs benefit" style="left:443px;top:2053px"><div class="abs corner"></div><div class="abs card">
  <svg width="74" height="60" viewBox="0 0 74 60" fill="none" stroke="#1d2433" stroke-width="2"><circle cx="36" cy="30" r="26" stroke="#f48b4f"/><circle cx="36" cy="30" r="20"/><text x="22" y="29" font-family="Montserrat,sans-serif" font-weight="700" font-size="8" fill="#1d2433" stroke="none">FOOD</text><text x="19" y="39" font-family="Montserrat,sans-serif" font-weight="700" font-size="8" fill="#1d2433" stroke="none">SAFETY</text><path d="M52 8l3 3 6-6" stroke="#f48b4f"/></svg>
  <div class="abs divider"></div><h4 class="abs">Food Safety &amp; Compliance</h4><p class="abs">Automate repetitive cooking tasks and reallocate staff to</p><a class="abs">Read More</a></div></div>
<div class="abs benefit" style="left:776px;top:2053px"><div class="abs corner"></div><div class="abs card">
  <svg width="74" height="60" viewBox="0 0 74 60" fill="none" stroke="#1d2433" stroke-width="2"><rect x="18" y="32" width="36" height="24" stroke="#f48b4f"/><path d="M14 32h44M30 32v24M42 32v24" stroke="#f48b4f"/><circle cx="36" cy="16" r="9"/><path d="M14 10h10v8H14z"/></svg>
  <div class="abs divider"></div><h4 class="abs">Lower Food Waste</h4><p class="abs">Tammo completes large-batch cooking significantly faster</p><a class="abs">Read More</a></div></div>

<a class="abs btn btn-book">Book a Demo</a>

<div class="abs media video" role="img" aria-label="Video preview of Tammo cooking a full batch from start to finish"></div>
<svg class="abs play" width="80" height="80" viewBox="0 0 80 80"><circle cx="40" cy="40" r="38" fill="#f48b4f" opacity=".75"/><circle cx="40" cy="40" r="26" fill="#f48b4f"/><path d="M33 28l16 12-16 12z" fill="#ffffff"/></svg>

<h2 class="abs section-title" style="top:2918px">What Our Partners <span class="accent">Are Saying</span></h2>

<svg class="abs arrow" style="left:43px" viewBox="0 0 24 24"><circle cx="12" cy="12" r="12" fill="#8a93a0"/><path d="M14 7l-5 5 5 5" fill="none" stroke="#fff" stroke-width="2.4"/></svg>
<svg class="abs arrow" style="left:1133px" viewBox="0 0 24 24"><circle cx="12" cy="12" r="12" fill="#0d2d5e"/><path d="M10 7l5 5-5 5" fill="none" stroke="#fff" stroke-width="2.4"/></svg>

<div class="abs quote-card" style="left:112px"><div class="abs avatar" role="img" aria-label="Portrait of Dana R."></div><span class="abs qmark">”</span><div class="abs name">Dana R.,</div><div class="abs role">Operations Director,</div>
  <svg class="abs stars" width="70" height="12" viewBox="0 0 70 12"><g fill="#f5a623"><path id="st" d="M6 0l1.8 4 4.2.4-3.2 2.8 1 4.2L6 9.2 2.2 11.4l1-4.2L0 4.4 4.2 4z"/><use href="#st" x="14"/><use href="#st" x="28"/><use href="#st" x="42"/><use href="#st" x="56"/></g></svg>
  <p class="abs">Tammo helped us reduce cooking times by 40% and nearly eliminate overcooking.</p></div>
<div class="abs quote-card" style="left:448px"><div class="abs avatar" role="img" aria-label="Portrait of Luis M."></div><span class="abs qmark">”</span><div class="abs name">Luis M.,</div><div class="abs role">VP of Culinary,</div>
  <svg class="abs stars" width="70" height="12" viewBox="0 0 70 12"><g fill="#f5a623"><use href="#st"/><use href="#st" x="14"/><use href="#st" x="28"/><use href="#st" x="42"/><use href="#st" x="56"/></g></svg>
  <p class="abs">We achieved consistent flavor across all six locations in under a month.</p></div>
<div class="abs quote-card" style="left:783px"><div class="abs avatar" role="img" aria-label="Portrait of Priya K."></div><span class="abs qmark">”</span><div class="abs name">Priya K.,</div><div class="abs role">CFO, GreenBowl Co.</div>
  <svg class="abs stars" width="70" height="12" viewBox="0 0 70 12"><g fill="#f5a623"><use href="#st"/><use href="#st" x="14"/><use href="#st" x="28"/><use href="#st" x="42"/><use href="#st" x="56"/></g></svg>
  <p class="abs">Training new kitchen staff used to take weeks. With Tammo, our onboarding time</p></div>

<footer class="abs site-footer">
  <div class="abs brand"><span class="mark"></span>KelvaTrix88</div>
  <div class="abs socials"><span></span><span></span><span></span><span></span></div>
  <div class="abs f-col" style="left:428px;top:90px"><h5>Quick Links</h5><ul>
    <li><span class="dot"></span>Home</li><li><span class="dot"></span>How Tammo Works</li><li><span class="dot"></span>Solutions</li><li><span class="dot"></span>Testimonials</li><li><span class="dot"></span>Pricing</li></ul></div>
  <div class="abs f-col" style="left:655px;top:90px"><h5>Legal</h5><ul>
    <li><span class="dot"></span>Privacy Policy</li><li><span class="dot"></span>Terms of Use</li><li><span class="dot"></span>Cookie Policy</li></ul></div>
  <div class="abs f-col" style="left:885px;top:90px;width:220px"><h5>Contact Us</h5><ul>
    <li><svg width="16" height="18" viewBox="0 0 16 18" style="margin-top:2px;flex:none"><path d="M8 0a7 7 0 017 7c0 5-7 11-7 11S1 12 1 7a7 7 0 017-7z" fill="#fff"/><circle cx="8" cy="7" r="2.6" fill="#0c2a57"/></svg>Harbor Lane. 218 Pier Ave, Portland, OR 97209,</li>
    <li style="margin-top:10px"><svg width="16" height="16" viewBox="0 0 16 16" style="margin-top:3px;flex:none"><circle cx="8" cy="8" r="8" fill="#fff"/><rect x="4" y="5" width="8" height="6" fill="none" stroke="#0c2a57" stroke-width="1.2"/><path d="M4 5l4 3 4-3" fill="none" stroke="#0c2a57" stroke-width="1.2"/></svg>support@tammokitchen.com</li>
    <li style="margin-top:10px"><svg width="16" height="16" viewBox="0 0 16 16" style="margin-top:3px;flex:none"><circle cx="8" cy="8" r="8" fill="#fff"/><path d="M5 4l2 2-1 1.5a6 6 0 002.5 2.5L10 9l2 2-1.5 1.5C7 12 4 9 3.5 5.5z" fill="#0c2a57"/></svg>0044-512907348</li></ul></div>
  <div class="abs f-rule"></div>
  <div class="abs copyright">© 2025 Tammo Technologies. All rights reserved.</div>
</footer>

</body>
</html>
```